Computer business require Thank you flyer to include in shipments

We ship computers (mainly laptops, tablets) to customers, most shipments are single unit in a box, we like to include in each box one page flyer as a Thank you note, and also mention in the note that for any reason if the buyer is not satisfied with the purchase or they wish to return the item they can contact us and will take care of any issue.
am thinking to have the design reflect a modern look, also with some color possibly to attract the customer attention and make them read the note, as some people tend to not read paper included in shipments. I will include the content that we like to be on the flyer, however we are open to suggestions either to add more text or how to layout the contents on the page. We also have a company logo that we would like to have it on the flyer.

Target Market(s)

End user, business buyers, wholesalers

Industry/Entity Type

Business

Font styles to use
Sans Serif
Other font styles liked:
• maybe even arial or times roman, a font that would be commonly used for a flyer easy readable

Colors
3377b5
f04a50
e667a6
b868aa
33a6d7
0792cd
ec1f27

Requirements
Must have
• Company logo
Nice to have
• Possible the address somewhere on the bottom of the page either left or right or one line at the end, depending how would look with the layout.
• Not too sure about color, most likely blue similar to our logo colors would be first choice, I was also thinking just to catch buyers attention when they open the package should we do it maybe red or even pink which would be softer tone possibly making it interesting for buyer to read. I know some colors would bring more attention to say "READ ME". Or maybe I'll have 2 flyers in different colors and sent to buyers accordingly based on the gender.
Should not have
• Somehow I did not realize we had added the note section on the content, I like to remove that part that mention about "Read Below Notes...." then the two paragraph that follow about technical guide. I just want this flyer be a Thank you note as well as inform buyers to contact us directly if they have issue.

```html
<!DOCTYPE html>
<html lang="en">
<head>
<meta charset="utf-8">
<title>Thank You Flyer</title>
<link href="https://fonts.googleapis.com/css2?family=Arimo:wght@400;700&display=swap" rel="stylesheet">
<style>
  :root {
    --blue-deep: #0b5fa5;
    --blue: #0792cd;
    --blue-light: #33a6d7;
    --blue-logo: #3377b5;
    --red: #ec1f27;
    --text: #2a2a2a;
    --white: #ffffff;
    --footer-bg: #f1f4f7;
    --photo-light: #f3f1ef;
    --photo-mid: #dcd8d5;
    --photo-cool: #c8ccd2;
  }
  * { margin: 0; padding: 0; box-sizing: border-box; }
  html, body { width: 849px; height: 1200px; overflow: hidden; background: var(--white); }
  body { font-family: "Arimo", Arial, sans-serif; color: var(--text); }
  .flyer { position: relative; width: 849px; height: 1200px; overflow: hidden; background: var(--white); }

  .hero-photo {
    position: absolute; left: 0; top: 0; width: 849px; height: 400px;
    background: linear-gradient(90deg, var(--white) 0%, var(--photo-light) 25%, var(--photo-mid) 65%, var(--photo-cool) 100%);
  }

  .brand { position: absolute; left: 38px; top: 26px; }
  .brand-row { display: flex; align-items: center; gap: 8px; }
  .brand-mark { width: 22px; height: 22px; background: var(--blue-logo); }
  .brand-name { font-size: 26px; font-weight: 700; color: var(--blue-logo); letter-spacing: 1px; line-height: 1; }
  .brand-tagline { margin-top: 8px; font-size: 11px; color: var(--red); }

  .band { position: absolute; left: 0; top: 230px; width: 849px; height: 220px; }
  .band-title {
    position: absolute; left: 40px; top: 352px;
    font-size: 40px; font-weight: 700; color: var(--white); letter-spacing: 1px; line-height: 1;
  }

  .letter {
    position: absolute; left: 40px; top: 450px; width: 770px;
    font-size: 14px; line-height: 1.6;
  }
  .letter p { margin-bottom: 16px; }
  .letter strong { font-weight: 700; }

  .closing-band {
    position: absolute; left: 0; top: 900px; width: 849px; height: 222px;
    background: linear-gradient(180deg, var(--blue) 0%, var(--blue-deep) 100%);
  }

  .footer {
    position: absolute; left: 0; top: 1122px; width: 849px; height: 78px;
    background: var(--footer-bg); text-align: center; padding-top: 16px;
  }
  .footer-contacts { font-size: 13px; color: var(--red); }
  .footer-contacts .sep { margin: 0 10px; }
  .footer-address { margin-top: 8px; font-size: 13px; color: var(--blue-deep); }
</style>
</head>
<body>
<main class="flyer">
  <div class="hero-photo" role="img" aria-label="Photo of a smiling family gathered around a laptop on a sofa"></div>

  <header class="brand">
    <div class="brand-row">
      <span class="brand-mark"></span>
      <span class="brand-name">NOVATEK INTERNATIONAL</span>
    </div>
    <div class="brand-tagline">Computer &amp; Electronics Wholesaler</div>
  </header>

  <svg class="band" viewBox="0 0 849 220" aria-hidden="true">
    <defs>
      <linearGradient id="bandGrad" x1="0" y1="0" x2="1" y2="0">
        <stop offset="0" stop-color="#0b5fa5"/>
        <stop offset="0.6" stop-color="#0792cd"/>
        <stop offset="1" stop-color="#33a6d7"/>
      </linearGradient>
    </defs>
    <path d="M0 60 C300 48 600 18 849 0 L849 130 C600 162 320 185 0 200 Z" fill="url(#bandGrad)"/>
    <path d="M0 200 C320 185 600 162 849 130 L849 142 C600 174 320 196 0 210 Z" fill="#33a6d7" opacity="0.45"/>
  </svg>
  <h1 class="band-title">THANK YOU</h1>

  <section class="letter">
    <p>Dear Customer,</p>
    <p>Thank you for your purchase. We very much appreciate your business, it has been a pleasure serving you.</p>
    <p><strong>Customer satisfaction is our #1 priority</strong>, at the same time our commitment is to provide quality products with exceptional customer service. We hope you have received your item in good condition and in a timely manner.</p>
    <p>We respectfully ask if you are in any way unhappy with your purchase, either having remorse, change of mind or an issue with the item received even during warranty period, please contact us directly via email at customerservices@novatek-example.com or call us Toll Free at (888) 555-0142 during business hours Monday - Friday, 9am to 4pm PST and give us the opportunity to make it right for you, we are committed to ensuring that you are completely satisfied with your purchase, appreciate your patience until we solve any issue, we value your business and would like to address your concern as quickly as possible.</p>
    <p>If you have been satisfied with our product and service we would greatly appreciate a moment of your time to leave your positive feedback for this transaction on the website of purchase, your opinion would allow us to maintain our high standards in providing a wonderful buying experience for all customers.</p>
  </section>

  <div class="closing-band" aria-hidden="true"></div>

  <footer class="footer">
    <div class="footer-contacts">
      <span>sales@novatek-example.com</span><span class="sep">|</span>
      <span>www.novatek-example.com</span><span class="sep">|</span>
      <span>Toll Free : 1-888-555-0142</span>
    </div>
    <div class="footer-address">2480 W. Larkspur Ave., Fairview, CA 90000</div>
  </footer>
</main>
</body>
</html>
```